Business Card For Halvenmoor Financial Consulting

Hi, I would like a business card designed. Bold, modern.
Please use the same design as the logo. I have also attached the website design to see the overall theme.
Wordmark Font
Color: Hex: #01AEF7

```html
<!DOCTYPE html>
<html lang="en">
<head>
<meta charset="utf-8">
<title>Halvenmoor Financial Consulting – Business Card</title>
<link href="https://fonts.googleapis.com/css2?family=Montserrat:wght@400;500;700;800&display=swap" rel="stylesheet">
<style>
  :root {
    --brand-blue: #01aef7;
    --line-blue: #1f8fd6;
    --navy-deep: #031a33;
    --navy-mid: #0a4f86;
    --card-dark: #16202a;
    --card-dark-2: #1c2833;
    --ink-dark: #0b1420;
    --text-light: #e9eef3;
    --text-muted: #c5d0da;
    --page-bg: #e4e5e8;
  }
  * { box-sizing: border-box; margin: 0; padding: 0; }
  html, body {
    width: 1200px; height: 800px; overflow: hidden;
    background: var(--page-bg);
    font-family: "Montserrat", Arial, sans-serif;
  }
  .stage {
    position: relative; width: 1200px; height: 800px;
    display: flex; align-items: center; justify-content: center; gap: 56px;
  }
  .card {
    position: relative; width: 525px; height: 300px;
    border-radius: 4px; overflow: hidden;
    box-shadow: 0 10px 28px rgba(0,0,0,.18);
  }

  /* Front side */
  .card--front {
    background: linear-gradient(150deg, var(--brand-blue) 0%, #1a8fd8 30%, var(--navy-mid) 62%, var(--navy-deep) 100%);
  }
  .wordmark { line-height: 1.05; text-transform: uppercase; font-weight: 800; }
  .wordmark__name { display: block; font-size: 40px; letter-spacing: 1px; }
  .wordmark__sub { display: block; font-size: 11.5px; letter-spacing: 5.2px; margin-top: 4px; }
  .card--front .wordmark {
    position: absolute; left: 50%; top: 112px; transform: translateX(-50%);
    color: var(--ink-dark); white-space: nowrap;
  }

  /* Back side */
  .card--back {
    background: linear-gradient(160deg, var(--card-dark) 0%, var(--card-dark-2) 100%);
    color: var(--text-light);
  }
  .card--back .wordmark { position: absolute; top: 34px; right: 38px; color: #ffffff; white-space: nowrap; }
  .card--back .wordmark__name { font-size: 34px; }
  .card--back .wordmark__sub { font-size: 10px; letter-spacing: 4.4px; }

  .holder { position: absolute; top: 124px; right: 150px; text-align: center; }
  .holder__name { color: var(--brand-blue); font-weight: 700; font-size: 17px; letter-spacing: .5px; text-transform: uppercase; }
  .holder__role { color: var(--text-muted); font-weight: 500; font-size: 11px; margin-top: 2px; }

  .divider { position: absolute; left: 22px; right: 22px; top: 176px; height: 1px; background: var(--line-blue); }

  .contact { position: absolute; list-style: none; font-size: 12px; font-weight: 500; line-height: 1.5; }
  .contact li { display: flex; align-items: flex-start; gap: 8px; }
  .contact svg { width: 12px; height: 12px; margin-top: 3px; flex: none; fill: var(--brand-blue); }
  .contact--left { left: 24px; top: 196px; }
  .contact--right { right: 24px; bottom: 28px; text-align: right; }
  .contact--right li { justify-content: flex-end; }
</style>
</head>
<body>
<main class="stage">

  <section class="card card--front" aria-label="Business card front">
    <div class="wordmark">
      <span class="wordmark__name">Halvenmoor</span>
      <span class="wordmark__sub">Financial Consulting</span>
    </div>
  </section>

  <section class="card card--back" aria-label="Business card back">
    <div class="wordmark">
      <span class="wordmark__name">Halvenmoor</span>
      <span class="wordmark__sub">Financial Consulting</span>
    </div>

    <div class="holder">
      <p class="holder__name">Marcus Bell</p>
      <p class="holder__role">Manager</p>
    </div>

    <div class="divider" aria-hidden="true"></div>

    <ul class="contact contact--left">
      <li>
        <svg viewBox="0 0 24 24" aria-hidden="true"><path d="M6.6 10.8a15.1 15.1 0 0 0 6.6 6.6l2.2-2.2c.3-.3.7-.4 1-.2 1.1.4 2.3.6 3.6.6.6 0 1 .4 1 1V20c0 .6-.4 1-1 1A17 17 0 0 1 3 4c0-.6.4-1 1-1h3.5c.6 0 1 .4 1 1 0 1.3.2 2.5.6 3.6.1.3 0 .7-.2 1z"/></svg>
        <span>(025) 481 27354</span>
      </li>
      <li>
        <svg viewBox="0 0 24 24" aria-hidden="true"><path d="M12 2a7 7 0 0 0-7 7c0 5.2 7 13 7 13s7-7.8 7-13a7 7 0 0 0-7-7zm0 9.5A2.5 2.5 0 1 1 12 6.5a2.5 2.5 0 0 1 0 5z"/></svg>
        <span>1286 Corbel Street<br>Dunmere, FL 32410</span>
      </li>
    </ul>

    <ul class="contact contact--right">
      <li>
        <span>info@halvenmoorconsulting.com</span>
        <svg viewBox="0 0 24 24" aria-hidden="true"><path d="M3 5h18c.6 0 1 .4 1 1v12c0 .6-.4 1-1 1H3c-.6 0-1-.4-1-1V6c0-.6.4-1 1-1zm9 7 8-5H4z"/></svg>
      </li>
      <li>
        <span>www.halvenmoorconsulting.com</span>
        <svg viewBox="0 0 24 24" aria-hidden="true"><path d="M12 2a10 10 0 1 0 0 20 10 10 0 0 0 0-20zm6.9 9h-3a15 15 0 0 0-1.3-6A8 8 0 0 1 18.9 11zM12 4.1c.9 1.2 1.7 3.6 1.9 6.9h-3.8c.2-3.3 1-5.7 1.9-6.9zM9.4 5a15 15 0 0 0-1.3 6h-3A8 8 0 0 1 9.4 5zm-4.3 8h3a15 15 0 0 0 1.3 6A8 8 0 0 1 5.1 13zm6.9 6.9c-.9-1.2-1.7-3.6-1.9-6.9h3.8c-.2 3.3-1 5.7-1.9 6.9zm2.6-.9a15 15 0 0 0 1.3-6h3a8 8 0 0 1-4.3 6z"/></svg>
      </li>
    </ul>
  </section>

</main>
</body>
</html>
```